Corporate Design für aufstrebende Immobilienmaklerin
Herr Kannert ist auf alle Wünsche eingegangen und hat meine Erwartungen an den Ablauf des Projektes in vielerlei Hinsicht übertroffen. Auch als es von meiner Seite Verzögerung gab, war er sehr verständnisvoll und hat gewartet, bis alles soweit war. Würde immer wieder mit ihm arbeiten.
Zielgruppe
Ich bin eine junge Immobilienmaklerin, die sich neu am Markt etablieren möchte.
Mein Service für Kunden umfasst das folgende Programm:
Wertermittlung
Marktanalyse
Energieausweis
Vermarktung
z.T. Home Staging
Vorbereitung Kaufverträge
Begleitung zum Notar...
Zielgruppe: Immobilienbesitzer, Käufer, Verkäufer, alle die gerne einen Mehrwert rund um die Immobilie haben möchten
Aufgabenstellung
Ich suche ein Design für meine Geschäftsunterlagen. Der Betrachter soll ein gutes Gefühl bekommen. Es soll seriös, edel und dynamisch wirken. Aber vor allem auch vertrauensvoll und kompetent.
Das Logo sollte unverwechselbar, einfach und einprägsam sein. Ich könnte mir sehr gut einen Schlüssel vorstellen, da es ja am Ende des gesamten Prozesses stets um eine Schlüsselübergabe geht. Aber da bin ich auch für alles andere offen.
Es wäre schön, wenn das Design in 'Wohlfühlfarben' gehalten ist, nicht so knallig, eher elegant.

```html
<!DOCTYPE html>
<html lang="de">
<head>
<meta charset="utf-8">
<title>Harwig Immobilien – Visitenkarte</title>
<link rel="stylesheet" href="https://fonts.googleapis.com/css2?family=Quicksand:wght@400;500;700&display=swap">
<style>
  :root {
    --page-bg: #e9e6e3;
    --card-white: #ffffff;
    --card-grey-light: #666666;
    --card-grey-dark: #474747;
    --rose: #a47d78;
    --rose-band: #b4948f;
    --band-light: #cfcac8;
    --text-grey: #9b9797;
    --front-text: #f2f0ef;
    --front-url: #b9b5b4;
    --photo-top: #f1f1f1;
    --photo-bottom: #c9ccd2;
    --deco: #f1efee;
  }
  * { box-sizing: border-box; margin: 0; padding: 0; }
  html, body {
    width: 1200px; height: 1200px; overflow: hidden;
    background: var(--page-bg);
    font-family: "Quicksand", sans-serif;
  }
  .sheet {
    width: 1200px; height: 1200px;
    display: flex; flex-direction: column; align-items: center; justify-content: center;
    gap: 60px;
  }
  .card {
    position: relative;
    width: 820px; height: 497px;
    overflow: hidden;
    box-shadow: 0 10px 28px rgba(0,0,0,0.16);
  }
  .card__band {
    position: absolute; left: 0; right: 0; bottom: 0; height: 22px;
    background: linear-gradient(to bottom, var(--band-light) 0 40%, var(--rose-band) 40% 100%);
  }

  /* Front */
  .card--front {
    background: radial-gradient(ellipse at 45% 40%, var(--card-grey-light), var(--card-grey-dark) 80%);
  }
  .card--front .brand {
    position: absolute; left: 0; right: 0; top: 190px;
    display: flex; align-items: center; justify-content: center; gap: 18px;
    color: var(--front-text);
  }
  .brand__dot {
    width: 26px; height: 26px; border-radius: 50%; background: currentColor;
  }
  .brand__name {
    font-weight: 500; font-size: 46px; letter-spacing: 4px; text-transform: uppercase;
  }
  .card--front .website {
    position: absolute; left: 0; right: 0; bottom: 56px;
    text-align: center; font-size: 18px; letter-spacing: 1px; color: var(--front-url);
  }
  .deco-circle {
    position: absolute; border-radius: 50%;
  }
  .card--front .deco-circle {
    right: -60px; top: 40px; width: 320px; height: 320px;
    background: rgba(255,255,255,0.035);
  }

  /* Back */
  .card--back { background: var(--card-white); }
  .card--back .deco-circle {
    right: 40px; top: 60px; width: 300px; height: 300px;
    background: var(--deco);
  }
  .card--back .brand {
    position: absolute; right: 48px; top: 42px;
    display: flex; align-items: center; gap: 12px;
    color: var(--rose);
  }
  .card--back .brand__dot { width: 18px; height: 18px; }
  .card--back .brand__name { font-size: 28px; letter-spacing: 2.5px; }
  .portrait {
    position: absolute; left: 60px; bottom: 22px;
    width: 330px; height: 400px;
    background: linear-gradient(to bottom, var(--photo-top), var(--photo-bottom));
  }
  .contact {
    position: absolute; left: 420px; top: 150px;
    color: var(--text-grey);
  }
  .contact__name {
    font-size: 30px; font-weight: 400; color: var(--rose); letter-spacing: 0.5px;
  }
  .contact__name strong { font-weight: 700; }
  .contact__role, .contact__lines, .contact__address {
    font-size: 18px; line-height: 1.3; letter-spacing: 0.4px;
  }
  .contact__role { margin-top: 6px; }
  .contact__lines { margin-top: 26px; }
  .contact__address { margin-top: 26px; }
</style>
</head>
<body>
<main class="sheet">
  <section class="card card--front" aria-label="Vorderseite der Visitenkarte">
    <div class="deco-circle"></div>
    <div class="brand">
      <span class="brand__dot"></span>
      <span class="brand__name">Harwig Immobilien</span>
    </div>
    <p class="website">www.harwig-immobilien.de</p>
    <div class="card__band"></div>
  </section>

  <section class="card card--back" aria-label="Rückseite der Visitenkarte">
    <div class="deco-circle"></div>
    <div class="brand">
      <span class="brand__dot"></span>
      <span class="brand__name">Harwig Immobilien</span>
    </div>
    <div class="portrait" role="img" aria-label="Porträtfoto der Maklerin im grauen Blazer vor hellem Hintergrund"></div>
    <div class="contact">
      <h1 class="contact__name">Lena <strong>Harwig</strong></h1>
      <p class="contact__role">Fachmaklerin der<br>Immobilienwirtschaft BFIM</p>
      <p class="contact__lines">Mobil: 0151-24 63 90 7<br>info@harwig-immobilien.de</p>
      <p class="contact__address">Lindenstieg 4<br>48231 Auenfeld</p>
    </div>
    <div class="card__band"></div>
  </section>
</main>
</body>
</html>
```